Lo Mara Menu Design Project

This project is pretty straight forward. You will be given 3 files which include the following:
1. Our proposed menu
2. Our Company logo
3. A sample menu on what we are looking for design wise

Your job is to create a visually pleasing menu that is simple, clean and fresh. Please refer to our home website for additional information. (www.lomara-eats.com) Must be in eps or equivalent format.

Target Market(s)

20s to 40s

Industry/Entity Type

It Company

Requirements
Must have
• Company log
Must be in EPS format

```html
<!DOCTYPE html>
<html lang="en">
<head>
<meta charset="utf-8">
<title>Lo Mara Menu Cover</title>
<link rel="stylesheet" href="https://fonts.googleapis.com/css2?family=Arimo:wght@400;700&family=Kalam:wght@400&display=swap">
<style>
  :root {
    --page-bg: #efefef;
    --cover-dark: #333335;
    --cover-edge: #1e1e1f;
    --accent-red: #ee3124;
    --ink-black: #0b0b0b;
    --silver: #c9c9c9;
    --white: #ffffff;
  }
  * { margin: 0; padding: 0; box-sizing: border-box; }
  html, body {
    width: 1200px;
    height: 1200px;
    overflow: hidden;
    background: var(--page-bg);
  }
  .menu-cover {
    position: absolute;
    left: 173px;
    top: 50px;
    width: 853px;
    height: 1100px;
    background: var(--cover-dark);
    border: 6px solid var(--cover-edge);
  }
  .menu-cover__texture {
    position: absolute;
    inset: 0;
    background: var(--cover-dark);
  }
  .menu-header {
    position: absolute;
    left: 130px;
    top: 178px;
    display: flex;
    gap: 6px;
  }
  .menu-header__icon-box {
    width: 154px;
    height: 154px;
    background: var(--ink-black);
    display: flex;
    align-items: center;
    justify-content: center;
  }
  .menu-header__band {
    width: 423px;
    height: 154px;
    background: var(--accent-red);
    padding: 14px 0 0 34px;
  }
  .menu-header__title {
    font-family: "Kalam", cursive;
    font-size: 84px;
    line-height: 1;
    color: var(--silver);
    font-weight: 400;
  }
  .menu-header__tagline {
    margin-top: 10px;
    font-family: "Arimo", sans-serif;
    font-size: 15px;
    color: var(--white);
  }
  .brand-mark {
    position: absolute;
    left: 0;
    right: 0;
    top: 700px;
    display: flex;
    align-items: center;
    justify-content: center;
    gap: 22px;
  }
  .brand-mark__square {
    width: 64px;
    height: 64px;
    background: var(--ink-black);
  }
  .brand-mark__name {
    font-family: "Arimo", sans-serif;
    font-weight: 700;
    font-size: 104px;
    line-height: 1;
    color: var(--accent-red);
  }
</style>
</head>
<body>
  <main class="menu-cover">
    <div class="menu-cover__texture" role="img" aria-label="Dark grey woven grid texture on the menu cover"></div>

    <header class="menu-header">
      <div class="menu-header__icon-box">
        <svg class="cutlery-icon" width="80" height="128" viewBox="0 0 80 128" aria-hidden="true">
          <g fill="#b5b5b5">
            <rect x="4" y="4" width="3" height="30" rx="1.5"/>
            <rect x="10" y="4" width="3" height="30" rx="1.5"/>
            <rect x="16" y="4" width="3" height="30" rx="1.5"/>
            <path d="M3 30 h17 v6 q0 8 -6 10 l-1 78 h-5 l-1 -78 q-6 -2 -6 -10 z"/>
            <ellipse cx="40" cy="26" rx="10" ry="22"/>
            <path d="M37.5 44 h5 l-0.5 80 h-4 z"/>
            <path d="M66 4 q12 10 10 50 l-6 2 l-1 68 h-5 l-1 -68 q-2 -30 3 -52 z"/>
          </g>
        </svg>
      </div>
      <div class="menu-header__band">
        <h1 class="menu-header__title">Menu</h1>
        <p class="menu-header__tagline">Experience the Art of Chinese Cuisine</p>
      </div>
    </header>

    <div class="brand-mark">
      <span class="brand-mark__square"></span>
      <span class="brand-mark__name">Lo Mara</span>
    </div>
  </main>
</body>
</html>
```